Therapy Dog Business need a brochure

I need a brochure designed for my Canine Assisted Therapy business in Victoria Australia. I have a logo already and info and photos to upload.
Best as white background and using the colours from the logo please
Updates

Hi Everyone,
I am sorry to have to revise the brief. I have added three new photos I was unable to add due to the size. I have had to wait for my photographer to change the size to add them today. I have been really inspired by all the work you have done so far. Thank you.
Could you please add the following on the brochure. (Under the individual dogs photo)
1. Pepper is the white dog. Please add the following under her picture. Pepper is one of the first Court Dogs in Australia. Working in Victoria, she has worked in the following Courts. The Halbrook Inquest Court, The Brindle Hearing Court in Collingwood, and the Fenwick Court in Melbourne CBD. Her ability to use her intuition for clients is inspiring. Please contact us for potential use in Courts. Pepper has worked at the Marlow Constabulary College, and at TALON at Mar Con. She is a stunning dog!
2. Barnaby is the golden dog. Barnaby is Peppers son, and had her instinct of intuition of who needs his help. Barnaby has an incredible soft approach as does his mother Pepper. He is incredibly safe with young children, and yet has a playful nature for adolescents and adults alike. He is soft and caring, and like his mother will go to those who need him most. Barnaby like his mother has worked at Marlow Constabulary, his time at MC included the Marlow Constabulary Directorate (MCD) Both he and his mother have very impressive CV'S!
3. Tansy the black dog. Tansy is my Therapy and Assistance dog "trainer" she is safe and stable with all the dogs and people I train for Therapy Dog Training and Assistance Dog Training. She has also been with me on my journey as a Counsellor and I have been able to work alongside her and Pepper for Counselling sessions.
She is soft, caring, and also intuitive. I am incredibly grateful for her help, as well as Pepper and Barnaby.
ALSO I am so sorry to add this but could you also add the following: Maybe in dot point?
Court Dog Availability
Therapy Dog Visits - Lawyers - Courts - Child Protection
Police Station / Ambulance Station / Fire Station - Visits
Private Therapy Dog Sessions
website and email confirmation coming soon. Thank you

Target Market(s)

First Responders

Requirements
Must have
• All the photos provided.
Should not have
• Generic photos

```html
<!DOCTYPE html>
<html lang="en">
<head>
<meta charset="utf-8">
<title>Tails of Comfort – Canine Assisted Therapy Brochure</title>
<link rel="stylesheet" href="https://fonts.googleapis.com/css2?family=Montserrat:wght@300;400;600;800&display=swap">
<style>
  :root {
    --backdrop: #d9d9db;
    --paper-edge: #fbfaf8;
    --panel: #eeebe6;
    --maroon: #4a1624;
    --body-text: #6f6560;
    --leaf-red: #a3311f;
    --frame: #ffffff;
    --golden: #b9782f;
    --cream-dog: #d9c7a6;
    --black-dog: #2a2a2c;
    --sofa: #7f8fd8;
    --brick: #a66a4c;
  }
  * { box-sizing: border-box; margin: 0; padding: 0; }
  html, body { width: 1200px; height: 1000px; overflow: hidden; }
  body {
    background: var(--backdrop);
    font-family: "Montserrat", sans-serif;
    position: relative;
  }
  .brochure {
    position: absolute;
    left: 45px; top: 70px;
    width: 1110px; height: 860px;
    display: flex;
    background: var(--paper-edge);
    box-shadow: 0 14px 40px rgba(0,0,0,.18);
  }
  .panel {
    position: relative;
    width: 370px; height: 100%;
    padding: 16px;
    border-right: 1px solid #e4e1dc;
  }
  .panel:last-child { border-right: none; }
  .panel-inner {
    position: relative;
    width: 100%; height: 100%;
    background: var(--panel);
    overflow: hidden;
  }
  .photo {
    position: absolute;
    background: var(--frame);
    padding: 7px;
    box-shadow: 0 6px 14px rgba(0,0,0,.25);
  }
  .photo .fill { width: 100%; height: 100%; }
  .photo--golden { left: 125px; top: 26px; width: 195px; height: 135px; transform: rotate(-3deg); }
  .photo--golden .fill { background: linear-gradient(135deg, #8fa27a, var(--golden) 55%, #6f4a22); }
  .photo--cream { left: 105px; top: 152px; width: 170px; height: 105px; transform: rotate(-3deg); }
  .photo--cream .fill { background: linear-gradient(135deg, #7c6d5c, var(--cream-dog) 60%, #8a7b68); }
  .photo--black { left: 22px; top: 222px; width: 150px; height: 120px; transform: rotate(-3deg); }
  .photo--black .fill { background: linear-gradient(160deg, #f2f2f2, #8d8d90 40%, var(--black-dog) 75%); }
  .photo--trio { left: 30px; top: 330px; width: 280px; height: 190px; transform: rotate(-3deg); }
  .photo--trio .fill { background: linear-gradient(180deg, var(--brick) 0 32%, var(--sofa) 32% 100%); }
  .leaf {
    position: absolute;
    width: 22px; height: 22px;
    background: var(--leaf-red);
    border-radius: 4px;
  }
  .leaf--left { left: 215px; top: 300px; }
  .leaf--right { left: 160px; top: 780px; }

  .dog-notes {
    position: absolute;
    left: 18px; right: 18px; top: 366px;
  }
  .dog-note { margin-bottom: 11px; }
  .dog-note h3, .services h3 {
    color: var(--maroon);
    font-weight: 600;
    font-size: 12px;
    letter-spacing: .04em;
    margin-bottom: 3px;
  }
  .dog-note p, .services li {
    color: var(--body-text);
    font-weight: 400;
    font-size: 9.5px;
    line-height: 1.42;
  }
  .services { margin-top: 4px; }
  .services ul { list-style: none; }
  .services li { padding-left: 12px; position: relative; }
  .services li::before {
    content: ""; position: absolute; left: 1px; top: 5px;
    width: 5px; height: 5px; border-radius: 50%;
    background: var(--leaf-red);
  }

  .headline {
    color: var(--maroon);
    font-weight: 800;
    font-size: 24px;
    line-height: 1.1;
    text-align: center;
    padding: 60px 20px 0;
  }
  .intro {
    color: var(--body-text);
    font-weight: 300;
    font-size: 15px;
    line-height: 1.75;
    text-align: center;
    margin-top: 22px;
  }
  .brand-mark { display: flex; flex-direction: column; align-items: center; }
  .brand-mark .dot {
    width: 56px; height: 56px; border-radius: 50%;
    border: 2px solid var(--maroon);
  }
  .brand-mark .name {
    color: var(--maroon);
    font-weight: 600;
    letter-spacing: .12em;
    text-transform: uppercase;
  }
  .contact-block { position: absolute; left: 0; right: 0; top: 600px; }
  .contact-block .brand-mark .name { font-size: 13px; margin-top: 16px; }
  .contact-lines {
    margin-top: 8px;
    text-align: center;
    color: var(--body-text);
    font-size: 11px;
    line-height: 1.5;
  }
  .contact-lines a { color: var(--body-text); }
  .cover-brand { position: absolute; left: 0; right: 0; top: 80px; }
  .cover-brand .dot { width: 150px; height: 150px; border-width: 3px; }
  .cover-brand .name { font-size: 18px; margin-top: 16px; }
  .cover-title {
    position: absolute; left: 0; right: 0; top: 590px;
    color: var(--maroon);
    font-weight: 600;
    font-size: 42px;
    line-height: 1.05;
    text-align: center;
  }
</style>
</head>
<body>
<main class="brochure">
  <section class="panel panel--gallery">
    <div class="panel-inner">
      <div class="photo photo--golden"><div class="fill" role="img" aria-label="Photo of Barnaby, the golden therapy dog, in profile"></div></div>
      <div class="photo photo--cream"><div class="fill" role="img" aria-label="Photo of Pepper, the white therapy dog, lying on a deck"></div></div>
      <div class="photo photo--black"><div class="fill" role="img" aria-label="Photo of Tansy, the black therapy dog"></div></div>
      <div class="leaf leaf--left" role="img" aria-label="Maple leaf ornament"></div>

      <div class="dog-notes">
        <article class="dog-note">
          <h3>Pepper</h3>
          <p>One of the first Court Dogs in Australia, Pepper has worked at the Halbrook Inquest Court, the Brindle Hearing Court in Collingwood and the Fenwick Court in Melbourne CBD, as well as the Marlow Constabulary College and TALON at Mar Con. Contact us about Court visits.</p>
        </article>
        <article class="dog-note">
          <h3>Barnaby</h3>
          <p>Pepper's son shares her intuition for who needs him most. Soft, caring and safe with young children, yet playful with adolescents and adults. He has worked with Marlow Constabulary, including the Marlow Constabulary Directorate (MCD).</p>
        </article>
        <article class="dog-note">
          <h3>Tansy</h3>
          <p>Our Therapy and Assistance Dog "trainer", safe and stable with every dog and person we train. Soft, caring and intuitive, she works alongside Pepper in our Counselling sessions.</p>
        </article>
        <div class="services">
          <h3>Our Services</h3>
          <ul>
            <li>Court Dog Availability</li>
            <li>Therapy Dog Visits – Lawyers – Courts – Child Protection</li>
            <li>Police, Ambulance &amp; Fire Station Visits</li>
            <li>Private Therapy Dog Sessions</li>
          </ul>
        </div>
      </div>
    </div>
  </section>

  <section class="panel panel--contact">
    <div class="panel-inner">
      <h2 class="headline">Join the Healing<br>Journey Today!</h2>
      <p class="intro">
        Whether you are seeking<br>emotional support or mental<br>health improvement,<br>Canine Assisted Therapy<br>offers a unique and<br>compassionate approach<br>to healing.<br>Connect with us today<br>to learn more about how<br>a therapy dog can help<br>enhance your life<br>and well-being.
      </p>
      <div class="contact-block">
        <div class="brand-mark">
          <span class="dot"></span>
          <span class="name">Tails of Comfort</span>
        </div>
        <p class="contact-lines">
          0400 217 364<br>
          <a href="#">www.tailsofcomfort.com</a><br>
          <a href="#">hello@tailsofcomfort.com</a>
        </p>
      </div>
    </div>
  </section>

  <section class="panel panel--cover">
    <div class="panel-inner">
      <div class="brand-mark cover-brand">
        <span class="dot"></span>
        <span class="name">Tails of Comfort</span>
      </div>
      <div class="photo photo--trio"><div class="fill" role="img" aria-label="Photo of Barnaby, Pepper and Tansy resting together on a blue couch"></div></div>
      <h1 class="cover-title">Canine<br>Assisted<br>Therapy</h1>
      <div class="leaf leaf--right" role="img" aria-label="Maple leaf ornament"></div>
    </div>
  </section>
</main>
</body>
</html>
```